BRN website video quote promotion tiles

We are promoting vehicle leasing by video, which contains several quotation examples imported from the video. We must re-vamp the quotation tiles, contact boxes, and contact form. The first tile is generated from the video, so this must be a separate project. We are looking for a welcoming, professional flow and leave color choices to design with an emphasis on communication prompts, and additional prompts in the design would be welcome.

Target Market(s)

Any Customer interaction from the tile quotes, contact, call, message,

Industry/Entity Type

vehicle leasing

Coding

Coded - Design and coding required

Number of Pages Required

1 page

Colors

Designer to choose colors to be used in the design.

Requirements
Must have
• emphasis on point of contact and visual impact on quote tile excluding main one
Should not have
• changes to the quote structure as these imported from video pricing no changes to main image as this template which can addressed as separate project

```html
<!DOCTYPE html>
<html lang="en">
<head>
<meta charset="utf-8">
<title>BRN Quote Tiles</title>
<link rel="stylesheet" href="https://fonts.googleapis.com/css2?family=Montserrat:wght@400;500;600&family=Open+Sans:wght@400&display=swap">
<style>
  :root {
    --bg: #f5f5f5;
    --orange: #e07f35;
    --ink: #1e1e1e;
    --frame: #8a8a8a;
    --divider: #3a3a3a;
    --red: #e02020;
    --badge-line: #e07f35;
    --green-soft: #7ccf6f;
    --green: #2aa81a;
    --white: #ffffff;
  }
  * { margin: 0; padding: 0; box-sizing: border-box; }
  html, body { width: 1200px; height: 224px; overflow: hidden; background: var(--bg); }
  body { font-family: "Montserrat", sans-serif; color: var(--ink); }
  .canvas { position: relative; width: 1200px; height: 224px; }
  .divider { position: absolute; top: 25px; width: 1px; height: 174px; background: var(--divider); }
  .title {
    position: absolute; font-weight: 600; font-size: 23px; color: var(--orange);
    line-height: 1; letter-spacing: 0.2px; white-space: nowrap; transform: translate(-50%, -50%);
  }
  .title.left { transform: translateY(-50%); }
  .terms {
    position: absolute; width: 300px; height: 45px; border: 1px solid var(--frame);
    border-radius: 6px; text-align: center; font-size: 17px; font-weight: 400; padding-top: 7px;
    white-space: nowrap;
  }
  .badge {
    position: absolute; width: 76px; height: 15px; background: var(--bg);
    border: 1px solid var(--badge-line); border-radius: 2px;
    font-family: "Open Sans", sans-serif; font-size: 8px; line-height: 13px;
    color: var(--red); text-align: center;
  }
  .price {
    position: absolute; font-weight: 600; font-size: 10px; white-space: nowrap;
    line-height: 1; transform: translateY(-50%);
  }
  .price .vat { font-weight: 400; font-size: 6.5px; margin-left: 2px; }
  .price.center { transform: translate(-50%, -50%); }
  .price.right { transform: translate(-100%, -50%); }
  .btn {
    position: absolute; width: 87px; height: 19px; border-radius: 4px;
    font-size: 8.5px; font-weight: 500; color: var(--white);
    text-align: center; line-height: 19px;
  }
  .btn.contact { background: var(--orange); }
  .btn.chat { background: var(--green-soft); }
  .chat-tile {
    position: absolute; width: 36px; height: 36px; border-radius: 3px; background: var(--green);
    color: var(--white); font-size: 7.5px; font-weight: 500; text-align: center; line-height: 36px;
  }
</style>
</head>
<body>
<div class="canvas">
  <!-- Tile one -->
  <section class="quote-tile">
    <h2 class="title" style="left:199px; top:51px;">CONTRACT HIRE</h2>
    <div class="terms" style="left:49px; top:76px;">3 years, 9+35, 10K miles annually</div>
    <div class="badge" style="left:161px; top:114px;">Not Maintained</div>
    <p class="price center" style="left:199px; top:144px;">£278.64<span class="vat">(PLUS VAT)</span></p>
    <div class="btn contact" style="left:48px; top:163px;">Contact Us</div>
    <div class="btn chat" style="left:263px; top:163px;">Chatly</div>
  </section>

  <div class="divider" style="left:400px;"></div>

  <!-- Tile two -->
  <section class="quote-tile">
    <h2 class="title left" style="left:431px; top:61px;">CONTRACT HIRE</h2>
    <p class="price right" style="left:770px; top:60px;">£278.64<span class="vat">(PLUS VAT)</span></p>
    <div class="terms" style="left:431px; top:85px;">3 years, 9+35, 10K miles annually</div>
    <div class="badge" style="left:544px; top:123px;">Not Maintained</div>
    <div class="btn contact" style="left:431px; top:151px;">Contact Us</div>
    <div class="chat-tile" style="left:734px; top:143px;">Chatly</div>
  </section>

  <div class="divider" style="left:801px;"></div>

  <!-- Tile three -->
  <section class="quote-tile">
    <h2 class="title" style="left:1001px; top:61px;">CONTRACT HIRE</h2>
    <div class="terms" style="left:851px; top:84px;">3 years, 9+35, 10K miles annually</div>
    <div class="badge" style="left:963px; top:122px;">Not Maintained</div>
    <div class="btn contact" style="left:832px; top:151px;">Contact Us</div>
    <p class="price center" style="left:1001px; top:161px;">£278.64<span class="vat">(PLUS VAT)</span></p>
    <div class="chat-tile" style="left:1135px; top:143px;">Chatly</div>
  </section>
</div>
</body>
</html>
```